New bussiness card, using company logo.
Lionel Brisk
Manager/Director
Brisk Property Developments
Po Box 5347
Thuringowa Central
Qld
0491 638 205
lionel@briskpropertydevelopments
eye catching, vibrant colours, professional

```html
<!DOCTYPE html>
<html lang="en">
<head>
<meta charset="utf-8">
<title>Brisk Property Developments – Business Card</title>
<link rel="stylesheet" href="https://fonts.googleapis.com/css2?family=PT+Sans:wght@400;700&display=swap">
<style>
  :root {
    --brand-red: #d9232e;
    --brand-green: #7cc242;
    --text-grey: #6d6e71;
    --card-white: #ffffff;
    --backdrop: #dfe5e8;
  }
  * { box-sizing: border-box; margin: 0; padding: 0; }
  html, body {
    width: 1200px;
    height: 960px;
    overflow: hidden;
    background: var(--backdrop);
    font-family: "PT Sans", Arial, sans-serif;
  }
  .sheet {
    width: 1200px;
    height: 960px;
    display: flex;
    flex-direction: column;
    align-items: center;
    justify-content: center;
    gap: 60px;
  }
  .card {
    position: relative;
    width: 660px;
    height: 400px;
    background: var(--card-white);
    box-shadow: 0 10px 28px rgba(40, 60, 70, 0.18);
    overflow: hidden;
  }
  /* Front */
  .card-front .brand-name {
    position: absolute;
    left: 40px;
    top: 48px;
    font-weight: 700;
    font-size: 44px;
    line-height: 1;
    letter-spacing: -0.5px;
    text-transform: uppercase;
    color: var(--brand-red);
  }
  .card-front .brand-name small {
    display: block;
    font-size: 26px;
    letter-spacing: 0.5px;
    margin-top: 6px;
  }
  .person {
    position: absolute;
    right: 44px;
    top: 176px;
    text-align: right;
  }
  .person-name {
    font-size: 24px;
    color: var(--text-grey);
    text-transform: uppercase;
    letter-spacing: 0.3px;
  }
  .person-role {
    font-size: 19px;
    color: var(--brand-red);
    margin-top: 4px;
  }
  .contact {
    position: absolute;
    left: 40px;
    top: 228px;
    color: var(--text-grey);
    font-size: 19px;
    line-height: 1.35;
  }
  .contact-line {
    display: flex;
    align-items: center;
    gap: 12px;
  }
  .contact-icon {
    width: 18px;
    height: 18px;
    flex: none;
  }
  .postal { margin-top: 12px; }
  .base-band {
    position: absolute;
    left: 0;
    right: 0;
    bottom: 0;
    height: 7px;
    background: var(--brand-green);
  }
  /* Back */
  .card-back {
    display: flex;
    align-items: center;
    justify-content: center;
  }
  .card-back .brand-name {
    font-weight: 700;
    font-size: 46px;
    line-height: 1;
    text-transform: uppercase;
    color: var(--brand-red);
    text-align: center;
  }
  .card-back .brand-name small {
    display: block;
    font-size: 27px;
    letter-spacing: 0.5px;
    margin-top: 8px;
  }
</style>
</head>
<body>
<main class="sheet">
  <section class="card card-front" aria-label="Business card front">
    <div class="brand-name">Brisk Property<small>Developments</small></div>

    <div class="person">
      <div class="person-name">Lionel Brisk</div>
      <div class="person-role">Manager/Director</div>
    </div>

    <div class="contact">
      <div class="contact-line">
        <svg class="contact-icon" viewBox="0 0 18 18" aria-hidden="true">
          <rect x="1" y="1" width="16" height="16" rx="3" fill="none" stroke="#7cc242" stroke-width="1.5"/>
          <path d="M6 4.5c-1 .6-1.5 1.6-1 3 .8 2.4 2.6 4.5 5 5.7 1.3.6 2.4.2 3-.8l-1.8-1.6-1.2.8c-1-.5-2-1.6-2.5-2.7l.8-1.1z" fill="#7cc242"/>
        </svg>
        <span>0491 638 205</span>
      </div>
      <div class="contact-line">
        <svg class="contact-icon" viewBox="0 0 18 18" aria-hidden="true">
          <rect x="1" y="1" width="16" height="16" rx="3" fill="none" stroke="#7cc242" stroke-width="1.5"/>
          <rect x="4" y="5.5" width="10" height="7" fill="#7cc242"/>
          <path d="M4 5.5l5 4 5-4" fill="none" stroke="#fff" stroke-width="1"/>
        </svg>
        <span>lionel@briskpropertydevelopments</span>
      </div>
      <div class="postal">
        Po Box 5347<br>
        Kelsford Heights, Qld
      </div>
    </div>

    <div class="base-band"></div>
  </section>

  <section class="card card-back" aria-label="Business card back">
    <div class="brand-name">Brisk Property<small>Developments</small></div>
  </section>
</main>
</body>
</html>
```